Home Refinance . Residential Mortgages

I want to post a small flyer as part of an email. I want do an email blast. I am a mortgage company and want to entice borrowers with my low interest rates. My website is www.brightmoorloans.example
The colors must match the website colors.
QX HPRL REFINANCE.
30 YR. FIXED RATES as low as
2.25% | 2.437% APR
No Appraisal, No out of Pocket cost, NO Income Verification, NO Asset Verification, Close in 30 days or less

Target Market(s)

Real Estate agents & Borrowers looking to get a mortgage loan

Colors
0455a3
ec1f27
28a1d5

Requirements
Must have
• The colors must match the website colors.
BRIGHTMOOR LOANS, INC,.
4817B Wrenhollow Road
Alexandria, VA 40587
RLCB 5830176
www.rlcbpublicregistry.example

Equal Housing Oppurtunity LOGO.

```html
<!DOCTYPE html>
<html lang="en">
<head>
<meta charset="utf-8">
<title>QX HPRL Refinance – Brightmoor Loans</title>
<link rel="stylesheet" href="https://fonts.googleapis.com/css2?family=Bebas+Neue&family=Lexend:wght@300;400&family=Poppins:wght@400&display=swap">
<style>
  :root {
    --page-bg: #f3f6f9;
    --navy-deep: #06215e;
    --navy: #0a2a6b;
    --blue-mid: #0455a3;
    --blue-light: #1f9ad2;
    --sky: #45c4ff;
    --cta-start: #0b5ea8;
    --cta-end: #22b8f0;
    --slate: #b4b5b8;
    --ink: #0a0a0a;
    --text-dark: #2a2a2a;
    --white: #ffffff;
  }
  * { box-sizing: border-box; margin: 0; padding: 0; }
  html, body {
    width: 1200px; height: 848px; overflow: hidden;
    background: var(--page-bg);
  }
  .flyer {
    position: absolute; left: 65px; top: 70px;
    width: 1069px; height: 708px;
    background: var(--white);
    box-shadow: 0 12px 40px rgba(20, 30, 50, 0.18);
    overflow: hidden;
    font-family: 'Lexend', sans-serif;
    color: var(--white);
  }
  .flyer-shapes { position: absolute; inset: 0; }
  .flyer p, .flyer h1 { line-height: 1; white-space: nowrap; }
  .headline-kicker {
    position: absolute; left: 95px; top: 113px;
    font-size: 24px; font-weight: 400; letter-spacing: 0.8px;
  }
  .headline-main {
    position: absolute; left: 91px; top: 190px;
    font-family: 'Bebas Neue', sans-serif; font-weight: 400;
    font-size: 98px; letter-spacing: 0;
    color: var(--sky);
  }
  .rate-lead {
    position: absolute; left: 90px; top: 318px;
    font-size: 26px; font-weight: 300; letter-spacing: 4px;
  }
  .rate-row {
    position: absolute; left: 86px; top: 388px;
    display: flex; align-items: center; height: 52px;
    font-size: 33px; font-weight: 400; letter-spacing: 1.5px;
    white-space: nowrap;
  }
  .rate-divider {
    width: 2px; height: 50px; margin: 0 33px 0 33px;
    background: var(--sky); border-radius: 1px;
  }
  .benefits {
    position: absolute; left: 85px; top: 519px;
    list-style: none; white-space: nowrap;
    font-size: 13px; font-weight: 300; letter-spacing: 1.6px;
    line-height: 29px; text-transform: uppercase;
  }
  .benefits .emphasis { font-weight: 400; letter-spacing: 1px; }
  .site-url {
    position: absolute; left: 839px; top: 42px;
    transform: translateX(-50%);
    font-family: 'Poppins', sans-serif;
    font-size: 18px; letter-spacing: 3px;
    color: var(--text-dark);
  }
  .cta-button {
    position: absolute; left: 677px; top: 631px;
    width: 280px; height: 62px; border-radius: 31px;
    background: linear-gradient(90deg, var(--cta-start), var(--cta-end));
    display: flex; align-items: center; justify-content: center; gap: 18px;
    font-size: 21px; letter-spacing: 3.2px; color: var(--white);
    text-decoration: none; white-space: nowrap;
  }
  .cta-button svg { width: 26px; height: 26px; }
</style>
</head>
<body>
  <main class="flyer">
    <svg class="flyer-shapes" viewBox="0 0 1069 708" width="1069" height="708">
      <defs>
        <linearGradient id="panelBlue" x1="0" y1="0" x2="0.35" y2="1">
          <stop offset="0" stop-color="#0c2b6e"/>
          <stop offset="0.45" stop-color="#082462"/>
          <stop offset="1" stop-color="#1f98cf"/>
        </linearGradient>
        <linearGradient id="photoTones" x1="0" y1="0" x2="1" y2="1">
          <stop offset="0" stop-color="#2a2d36"/>
          <stop offset="0.45" stop-color="#4a4d57"/>
          <stop offset="0.75" stop-color="#a69483"/>
          <stop offset="1" stop-color="#d8d6d3"/>
        </linearGradient>
      </defs>
      <rect class="slate-strip" x="0" y="93" width="1069" height="615" fill="var(--slate)"/>
      <polygon class="photo-area" role="img" aria-label="Photo of a loan officer in a suit handing over house keys at a desk with documents, a calculator and a small model house"
               points="583,93 1069,93 1069,615 562,615" fill="url(#photoTones)"/>
      <polygon class="cta-band" points="562,615 1069,615 1069,708 552,708" fill="var(--ink)"/>
      <polygon class="offer-panel" points="0,0 591,0 529,708 0,708" fill="url(#panelBlue)"/>
    </svg>

    <p class="headline-kicker">QX HPRL REFINANCE</p>
    <h1 class="headline-main">FIXED RATES</h1>
    <p class="rate-lead">as low as</p>
    <div class="rate-row">
      <span class="rate-note">2.25%</span>
      <span class="rate-divider"></span>
      <span class="rate-apr">2.437% APR</span>
    </div>

    <ul class="benefits">
      <li>No appraisal, no out of pocket cost,</li>
      <li>No income verification, no asset verification,</li>
      <li class="emphasis">Close in 30 days or less</li>
    </ul>

    <p class="site-url">www.brightmoorloans.example</p>

    <a class="cta-button" href="#">
      <span>GET STARTED</span>
      <svg viewBox="0 0 26 26" aria-hidden="true">
        <polyline points="4,3 13,13 4,23" fill="none" stroke="#fff" stroke-width="2.4" stroke-linecap="round" stroke-linejoin="round"/>
        <polyline points="13,3 22,13 13,23" fill="none" stroke="#fff" stroke-width="2.4" stroke-linecap="round" stroke-linejoin="round"/>
      </svg>
    </a>
  </main>
</body>
</html>
```